We need a web page design for a new company called "Brambel". We provide an innovative music sharing mobile application that allows music listeners to share their music without paying for a monthly subscription. We would like to incorporate the attached logo and color scheme. The final design should communicate music gifting and sharing.

Industry/Entity Type

It Company

```html
<!DOCTYPE html>
<html lang="en">
<head>
<meta charset="utf-8">
<title>Brambel – Music Sharing App</title>
<link href="https://fonts.googleapis.com/css2?family=Arvo:wght@700&family=Lato:wght@400;700;900&display=swap" rel="stylesheet">
<style>
:root{
  --green:#5aa51a;
  --green-dark:#4a8d12;
  --ink:#222;
  --muted:#666;
  --light:#999;
  --dark:#1b1b1b;
  --white:#fff;
}
*{margin:0;padding:0;box-sizing:border-box}
html,body{width:1200px;height:2981px;overflow:hidden}
body{font-family:"Lato",sans-serif;color:var(--ink);background:var(--white);position:relative}
a{color:inherit;text-decoration:none}

/* header */
.site-header{position:absolute;top:0;left:0;width:1200px;height:95px;background:var(--green)}
.brand-name{position:absolute;left:132px;top:28px;font-family:"Lato",sans-serif;font-weight:700;font-size:34px;line-height:1;color:var(--white)}
.main-nav{position:absolute;right:130px;top:0;display:flex;height:95px}
.main-nav a{display:flex;align-items:center;padding:0 18px;color:var(--white);font-size:15px}
.main-nav a.active{background:var(--white);color:var(--green);font-weight:700}
.caret{margin-left:6px;font-size:10px}

/* hero */
.hero{position:absolute;top:95px;left:0;width:1200px;height:530px;background:radial-gradient(ellipse at 35% 55%,#1f6fb8 0%,#0b2c55 30%,#05070e 65%)}
.hero-title{position:absolute;left:130px;top:150px;font-family:"Arvo",serif;font-size:38px;color:var(--white)}
.hero-sub{position:absolute;left:130px;top:210px;width:420px;font-size:17px;font-weight:700;line-height:26px;color:var(--white)}
.btn-now{position:absolute;left:130px;top:283px;width:154px;height:50px;background:var(--green);color:var(--white);font-weight:900;font-size:18px;display:flex;align-items:center;justify-content:center}
.hero-phone{position:absolute;left:735px;top:0;width:340px;height:530px;background:linear-gradient(160deg,#2b2b2b,#111 50%,#3a2a22)}

/* section titles */
.section-title{position:absolute;left:0;width:1200px;text-align:center;font-size:28px;font-weight:700}
.divider{position:absolute;left:500px;width:200px;height:14px}

/* welcome */
.welcome-img{position:absolute;left:130px;top:770px;width:410px;height:210px;background:linear-gradient(135deg,#eee,#cfcfd4 60%,#8a6f88)}
.welcome-text{position:absolute;left:630px;top:748px;width:440px;font-size:14px;line-height:22px;color:var(--muted)}
.more{color:var(--green);font-weight:700}
.stats{position:absolute;left:630px;top:885px;width:440px;display:flex;justify-content:space-between}
.stat{width:90px;text-align:center}
.stat-ico{width:60px;height:60px;border-radius:50%;background:var(--green);margin:0 auto 8px}
.stat-num{font-size:18px;font-weight:700}
.stat-lab{font-size:11px;color:var(--light)}

/* features */
.features{position:absolute;top:1045px;left:0;width:1200px;height:360px;background:radial-gradient(ellipse at 50% 50%,#5a5a5a,#1d1d1d 70%)}
.features .section-title{top:50px;color:var(--white)}
.feature{position:absolute;top:130px;width:170px;text-align:center;color:var(--white);font-size:17px;font-weight:700;line-height:30px}
.feature-ico{width:108px;height:108px;border-radius:50%;border:3px solid rgba(255,255,255,.8);margin:0 auto 14px;display:flex;align-items:center;justify-content:center}
.feature-ico span{width:84px;height:84px;border-radius:50%;background:rgba(255,255,255,.25);display:flex;align-items:center;justify-content:center}

/* how it works */
.how-img{position:absolute;left:170px;top:1530px;width:430px;height:565px;background:linear-gradient(180deg,#f2f2f2,#d9d9d9 30%,#e0b89a 70%,#c99b7a)}
.how-text{position:absolute;left:630px;top:1535px;width:440px;font-size:14px;line-height:22px;color:var(--muted)}
.step{position:absolute;left:630px;width:440px}
.step-ico{position:absolute;left:0;top:0;width:84px;height:84px;border-radius:14px;background:var(--green);display:flex;align-items:center;justify-content:center}
.step-body{position:absolute;left:108px;top:2px;width:330px;font-size:14px;line-height:22px;color:var(--muted)}
.step-body h3{font-size:17px;color:var(--ink);margin-bottom:6px}

/* reviews */
.reviews{position:absolute;top:2095px;left:0;width:1200px;height:305px;background:linear-gradient(180deg,#a8a8a8,#dedede 45%,#ececec)}
.reviews .section-title{top:55px}
.reviews-lead{position:absolute;top:132px;left:0;width:1200px;text-align:center;font-size:14px;color:#444}
.avatar{position:absolute;left:263px;top:175px;width:76px;height:76px;border-radius:50%;background:#b9c0c8;border:3px solid var(--white)}
.review{position:absolute;left:358px;top:175px;width:580px;font-size:14px;line-height:22px;color:#333}
.review h4{font-size:17px;margin-bottom:6px}
.arrow{position:absolute;top:205px}

/* contact */
.contact{position:absolute;top:2400px;left:0;width:1200px;height:445px;background:linear-gradient(135deg,#2e2e2e,#1e1e1e 50%,#2a2a2a)}
.contact h2{position:absolute;left:130px;top:56px;font-size:28px;font-weight:400;color:var(--white)}
.contact-lead{position:absolute;left:130px;top:98px;width:610px;font-size:14px;line-height:22px;color:var(--white)}
.field{position:absolute;height:34px;border:1px solid #ccc;background:var(--white);font-size:11px;color:#555;padding:10px 8px}
.btn-submit{position:absolute;left:130px;top:352px;width:106px;height:38px;border:2px solid var(--white);color:var(--white);font-weight:700;font-size:17px;display:flex;align-items:center;justify-content:center}
.share-lead{position:absolute;left:795px;top:98px;width:270px;font-size:12px;line-height:20px;color:var(--white)}
.social{position:absolute;left:795px;display:flex;align-items:center;gap:14px;color:var(--white);font-size:14px}
.social span{width:46px;height:46px;border-radius:50%;border:2px solid var(--white)}

/* footer */
.site-footer{position:absolute;top:2845px;left:0;width:1200px;height:108px;background:var(--green);color:var(--white);font-size:12px;line-height:18px}
.foot-addr{position:absolute;left:130px;top:20px;display:flex;gap:10px}
.foot-info{position:absolute;left:355px;top:20px}
.foot-info div{display:flex;gap:10px;align-items:center;margin-bottom:4px}
.foot-brand{position:absolute;right:130px;top:32px;font-family:"Lato",sans-serif;font-weight:700;font-size:34px;line-height:1;color:var(--white)}
.copyright{position:absolute;top:2953px;left:0;width:1200px;height:28px;background:var(--dark);color:#ccc;font-size:12px;text-align:center;line-height:28px}
</style>
</head>
<body>

<header class="site-header">
  <div class="brand-name">Brambel</div>
  <nav class="main-nav">
    <a class="active" href="#">Home</a>
    <a href="#">About<span class="caret">▼</span></a>
    <a href="#">How It Work</a>
    <a href="#">Download<span class="caret">▼</span></a>
    <a href="#">Join</a>
    <a href="#">Contact</a>
  </nav>
</header>

<section class="hero">
  <h1 class="hero-title">Get Brambels Music App Free</h1>
  <p class="hero-sub">We Provide Best Innovative Music Sharing Mobile Application</p>
  <a class="btn-now" href="#">NOW!</a>
  <div class="hero-phone" role="img" aria-label="Hand holding a phone showing the Brambel app download screen"></div>
</section>

<h2 class="section-title" style="top:675px">Welcome to Brambel</h2>
<svg class="divider" style="top:720px" viewBox="0 0 200 14"><line x1="0" y1="7" x2="90" y2="7" stroke="#ccc"/><line x1="110" y1="7" x2="200" y2="7" stroke="#ccc"/><circle cx="100" cy="7" r="4" fill="#333"/></svg>
<div class="welcome-img" role="img" aria-label="Tablet showing the Brambel music player"></div>
<p class="welcome-text">Lorem ipsum dolor sit amet, consectetuer adipiscing elit, sed diam nonummy nibh euismod tincidunt ut laoreet dolore magna aliquam erat volutpat. Ut wisi enim ad minim veniam, quis nostrud exerci tation ullamcorper suscipit lobortis nisl ut aliquip ex ea commodo consequat...<span class="more">READ MORE&gt;&gt;</span></p>
<div class="stats">
  <div class="stat"><div class="stat-ico"></div><div class="stat-num">9920</div><div class="stat-lab">DOWNLOADS</div></div>
  <div class="stat"><div class="stat-ico"></div><div class="stat-num">999</div><div class="stat-lab">DROIDEX USER</div></div>
  <div class="stat"><div class="stat-ico"></div><div class="stat-num">938</div><div class="stat-lab">POMOS USER</div></div>
  <div class="stat"><div class="stat-ico"></div><div class="stat-num">738</div><div class="stat-lab">BLEEP USER</div></div>
</div>

<section class="features">
  <h2 class="section-title">Features and benefits</h2>
  <svg class="divider" style="top:95px" viewBox="0 0 200 14"><line x1="0" y1="7" x2="90" y2="7" stroke="#888"/><line x1="110" y1="7" x2="200" y2="7" stroke="#888"/><circle cx="100" cy="7" r="4" fill="#fff"/></svg>
  <div class="feature" style="left:124px"><div class="feature-ico"><span><svg width="44" height="44" viewBox="0 0 44 44"><circle cx="22" cy="22" r="17" fill="none" stroke="#fff" stroke-width="4"/><line x1="10" y1="34" x2="34" y2="10" stroke="#fff" stroke-width="4"/></svg></span></div>No Credit<br>Card Required</div>
  <div class="feature" style="left:320px"><div class="feature-ico"><span><svg width="44" height="44" viewBox="0 0 44 44"><rect x="10" y="20" width="24" height="18" rx="2" fill="#fff"/><path d="M15 20v-6a7 7 0 0 1 14 0" fill="none" stroke="#fff" stroke-width="4"/></svg></span></div>Unlimited<br>Access</div>
  <div class="feature" style="left:511px"><div class="feature-ico"><span><svg width="44" height="44" viewBox="0 0 44 44"><rect x="8" y="22" width="6" height="16" fill="#fff"/><rect x="19" y="12" width="6" height="26" fill="#fff"/><rect x="30" y="17" width="6" height="21" fill="#fff"/></svg></span></div>Productivity<br>Tracker</div>
  <div class="feature" style="left:707px"><div class="feature-ico"><span><svg width="44" height="44" viewBox="0 0 44 44"><circle cx="22" cy="22" r="16" fill="none" stroke="#fff" stroke-width="4"/><path d="M18 14v14a4 4 0 1 1-3-4M18 14l9 3" fill="none" stroke="#fff" stroke-width="3"/></svg></span></div>Multiple<br>Music Channels</div>
  <div class="feature" style="left:904px"><div class="feature-ico"><span><svg width="44" height="44" viewBox="0 0 44 44"><path d="M22 6l14 8v16l-14 8-14-8V14z" fill="none" stroke="#fff" stroke-width="3"/><path d="M17 22h10M23 17l5 5-5 5" fill="none" stroke="#fff" stroke-width="3"/></svg></span></div>Social<br>Share</div>
</section>

<h2 class="section-title" style="top:1458px">How It Works</h2>
<svg class="divider" style="top:1503px" viewBox="0 0 200 14"><line x1="0" y1="7" x2="90" y2="7" stroke="#ccc"/><line x1="110" y1="7" x2="200" y2="7" stroke="#ccc"/><circle cx="100" cy="7" r="4" fill="#333"/></svg>
<div class="how-img" role="img" aria-label="Hand holding a tablet with the Brambel playlist screen"></div>
<p class="how-text">Lorem ipsum dolor sit amet, consectetur adipiscing elit. Pellentesque sed finibus lectus. Ut in sapien id n rutrum lacinia id nec tellus. Etiam tempor leo eu vulputa auctor. In feugiat sollicitudin enim sit amet volutpat.</p>
<div class="step" style="top:1637px"><div class="step-ico"><svg width="44" height="44" viewBox="0 0 44 44"><circle cx="22" cy="22" r="12" fill="none" stroke="#fff" stroke-width="6" stroke-dasharray="5 4"/><circle cx="22" cy="22" r="5" fill="#fff"/></svg></div><div class="step-body"><h3>Install Apps</h3>Lorem ipsum dolor sit amet, consectetur adipiscing elit. Pellentesque sed finibus lectus.<br><span class="more">READ MORE&gt;&gt;</span></div></div>
<div class="step" style="top:1775px"><div class="step-ico"><svg width="44" height="44" viewBox="0 0 44 44"><rect x="15" y="14" width="14" height="24" rx="3" fill="#fff"/><rect x="18" y="6" width="8" height="8" fill="#fff"/></svg></div><div class="step-body"><h3>Store Your Track</h3>Lorem ipsum dolor sit amet, consectetur adipiscing elit. Pellentesque sed finibus lectus.<br><span class="more">READ MORE&gt;&gt;</span></div></div>
<div class="step" style="top:1913px"><div class="step-ico"><svg width="44" height="44" viewBox="0 0 44 44"><rect x="6" y="10" width="32" height="24" rx="2" fill="none" stroke="#fff" stroke-width="3"/><path d="M18 16l9 6-9 6z" fill="#fff"/></svg></div><div class="step-body"><h3>Play Your Track</h3>Lorem ipsum dolor sit amet, consectetur adipiscing elit. Pellentesque sed finibus lectus.<br><span class="more">READ MORE&gt;&gt;</span></div></div>

<section class="reviews">
  <h2 class="section-title">App Reviews</h2>
  <svg class="divider" style="top:100px" viewBox="0 0 200 14"><line x1="0" y1="7" x2="90" y2="7" stroke="#999"/><line x1="110" y1="7" x2="200" y2="7" stroke="#999"/><circle cx="100" cy="7" r="4" fill="#333"/></svg>
  <p class="reviews-lead">Enim ad mini quis notrud exercitation ullamco laboris nisi ut aliqoido consegin reprehenderit.</p>
  <div class="avatar" role="img" aria-label="Reviewer portrait"></div>
  <div class="review"><h4>Culpa qui officia deserunt mollitlorum.</h4>Enim ad mini quis notrud exercitation ullamco laboris nisi ut aliqoido consegin reprehenderit in voluptate velit essle cillum dolore.</div>
  <svg class="arrow" style="left:128px" width="14" height="20" viewBox="0 0 14 20"><path d="M11 2L3 10l8 8" fill="none" stroke="#222" stroke-width="3"/></svg>
  <svg class="arrow" style="left:1056px" width="14" height="20" viewBox="0 0 14 20"><path d="M3 2l8 8-8 8" fill="none" stroke="#222" stroke-width="3"/></svg>
</section>

<section class="contact" role="img" aria-label="Dark city map background">
  <h2>Contact Us</h2>
  <p class="contact-lead">Lorem Ipsum is simply dummy text of the printing and typesetting industry. Lorem Ipsum has b industry's standard dummy text ever since the 1500s.</p>
  <div class="field" style="left:130px;top:174px;width:196px">First and Last Name</div>
  <div class="field" style="left:333px;top:174px;width:196px">Phone</div>
  <div class="field" style="left:536px;top:174px;width:200px">Email id</div>
  <div class="field" style="left:130px;top:240px;width:606px;height:88px">Type Here</div>
  <a class="btn-submit" href="#">SUBMIT</a>
  <h2 style="left:795px">Share With Us</h2>
  <p class="share-lead">Lorem Ipsum is simply dummy text of t printing and typesetting industry.</p>
  <div class="social" style="top:157px"><span></span>Facenote</div>
  <div class="social" style="top:219px"><span></span>Chirpit</div>
  <div class="social" style="top:281px"><span></span>Linkpro</div>
  <div class="social" style="top:343px"><span></span>Email</div>
</section>

<footer class="site-footer">
  <div class="foot-addr"><svg width="12" height="16" viewBox="0 0 12 16"><path d="M6 0a6 6 0 0 1 6 6c0 4-6 10-6 10S0 10 0 6a6 6 0 0 1 6-6z" fill="#fff"/><circle cx="6" cy="6" r="2" fill="#5aa51a"/></svg><div>Contrary to popular belief,<br>Lorem Ipsum is.<br>1234567</div></div>
  <div class="foot-info">
    <div><svg width="14" height="14" viewBox="0 0 14 14"><path d="M3 1l3 3-2 2a8 8 0 0 0 4 4l2-2 3 3-2 2C6 13 1 8 1 3z" fill="#fff"/></svg>Phone: 555 010 789</div>
    <div><svg width="14" height="14" viewBox="0 0 14 14"><rect x="1" y="5" width="12" height="8" fill="#fff"/><rect x="4" y="1" width="6" height="4" fill="#fff"/></svg>Fax: 555 010 789</div>
    <div><svg width="14" height="14" viewBox="0 0 14 14"><rect x="1" y="3" width="12" height="9" fill="#fff"/><path d="M1 3l6 5 6-5" fill="none" stroke="#5aa51a"/></svg>info@brambelmusic.com</div>
  </div>
  <div class="foot-brand">Brambel</div>
</footer>
<div class="copyright">Copyright © 2014 Brambelmusic.com. All Rights Reserved.</div>

</body>
</html>
```